Keystone Trench Co Business Card*

Looking for a professional, clean and crisp business card

I am in the underground utilities industry and am just looking for a really impressive business card. I would like our card to be white with our symbol crisp and clear with it protruding. I also have a business partner that will require his name and info on the card once the design is set. I would like to have our website info on the card which is;
http://keystonetrenchco.example/

Contact Information for Business Card

Website, contact name, number and email

```html
<!DOCTYPE html>
<html lang="en">
<head>
<meta charset="utf-8">
<title>Keystone Trench Co — Business Card</title>
<link rel="stylesheet" href="https://fonts.googleapis.com/css2?family=Bebas+Neue&family=Roboto+Condensed:wght@400&display=swap">
<style>
  :root {
    --backdrop: #1b1b1b;
    --kraft-light: #dcbd8f;
    --kraft-mid: #c49a66;
    --kraft-dark: #a27649;
    --ink: #141210;
    --icon-glyph: #d8b887;
  }
  * { margin: 0; padding: 0; box-sizing: border-box; }
  html, body {
    width: 1093px;
    height: 1200px;
    overflow: hidden;
    background: var(--backdrop);
  }
  .canvas {
    position: relative;
    width: 1093px;
    height: 1200px;
  }
  .card {
    position: absolute;
    left: 264px;
    width: 580px;
    height: 357px;
    background: linear-gradient(150deg, var(--kraft-light) 0%, var(--kraft-mid) 55%, var(--kraft-dark) 100%);
    color: var(--ink);
    text-align: center;
  }
  .card--front { top: 226px; }
  .card--back { top: 620px; }

  .contact-name {
    position: absolute;
    top: 94px;
    left: 0; right: 0;
    font-family: "Bebas Neue", sans-serif;
    font-size: 31px;
    line-height: 1;
    letter-spacing: 0.5px;
  }
  .contact-role {
    position: absolute;
    top: 125px;
    left: 0; right: 0;
    font-family: "Roboto Condensed", sans-serif;
    font-size: 19px;
    line-height: 1;
  }
  .icon-row {
    position: absolute;
    top: 167px;
    left: 0; right: 0;
    display: flex;
    justify-content: center;
    align-items: center;
    gap: 5px;
  }
  .icon-row .rule {
    width: 35px;
    height: 1px;
    background: var(--ink);
    margin: 0 4px;
  }
  .icon-row svg { display: block; }
  .contact-lines {
    position: absolute;
    top: 207px;
    left: 0; right: 0;
    font-family: "Roboto Condensed", sans-serif;
    font-size: 19px;
    line-height: 25.5px;
  }
  .brand-name {
    position: absolute;
    top: 50%;
    left: 0; right: 0;
    transform: translateY(-50%);
    font-family: "Bebas Neue", sans-serif;
    font-size: 52px;
    line-height: 1;
    letter-spacing: 1px;
    color: var(--ink);
  }
</style>
</head>
<body>
<main class="canvas">
  <section class="card card--front" aria-label="Business card front">
    <h1 class="contact-name">Marcus Hollings</h1>
    <p class="contact-role">Managing Director</p>
    <div class="icon-row">
      <span class="rule"></span>
      <svg width="26" height="26" viewBox="0 0 26 26" aria-label="Phone">
        <rect width="26" height="26" rx="3" fill="var(--ink)"/>
        <path d="M6 11 Q13 5 20 11 L18 13 L16 11 L10 11 L8 13 Z" fill="var(--icon-glyph)"/>
        <rect x="8" y="13" width="10" height="7" rx="1" fill="var(--icon-glyph)"/>
      </svg>
      <svg width="26" height="26" viewBox="0 0 26 26" aria-label="Email">
        <rect width="26" height="26" rx="3" fill="var(--ink)"/>
        <rect x="6" y="8" width="14" height="10" fill="none" stroke="var(--icon-glyph)" stroke-width="1.4"/>
        <path d="M6 8 L13 14 L20 8" fill="none" stroke="var(--icon-glyph)" stroke-width="1.4"/>
      </svg>
      <svg width="26" height="26" viewBox="0 0 26 26" aria-label="Website">
        <rect width="26" height="26" rx="3" fill="var(--ink)"/>
        <circle cx="13" cy="13" r="7" fill="var(--icon-glyph)"/>
        <path d="M10 9 Q13 11 11 14 Q13 16 12 19" fill="none" stroke="var(--ink)" stroke-width="1.6"/>
      </svg>
      <span class="rule"></span>
    </div>
    <p class="contact-lines">
      055-987 654 321<br>
      hello@keystonetrenchco.example<br>
      www.keystonetrenchco.example
    </p>
  </section>

  <section class="card card--back" aria-label="Business card back">
    <p class="brand-name">Keystone Trench Co</p>
  </section>
</main>
</body>
</html>
```